Create a wordpress website for Tovarin business solution

This project is to create a complete website with all pages.

Overview
The purpose of this project is to create a full complete website with all pages (16 pages). The site should be professional and modern. The site is for an IT recruiting and IT training company. The site needs to be easy to administer and update content. It should be simple to add pages, videos and testimonials later. I will leave the site layout, color schemes and flow to the designers.

Navigation Menu (Home, who we are, what we do, what makes us different, why it matters, candidate portal, contact us, Blog)

WHO WE ARE should be a drop down menu with link to pages (about us, mission, vision and purpose, our team)

WHAT WE DO should be drop down menu with link to the following pages (IT Recruiting, IT Training, Hardware and software sales)

What makes us different should be single page with different paragraph titles. (We live what we do, we don't compromise quality, we share knowledge, staffing guarantee)

Why it matters should be single page with paragraph titles. (Quickly fill positions, candidate career development)

Candidate portal should links to my portal login page. I can add the correct URL later. I just need it to link to somewhere. I can change it.

Contact us should have (address, phone number, google map and a form to submit request for a call back)

Blog - This link should launch a wordpress blogging module

Target Market(s)

IT RECRUITING AND CONSULTING

Industry/Entity Type

It Company

Coding

Coded - Design and coding required

Requirements
Must have
• Company Logo
• Navigation Menu (Home, who we are, what we do, what makes us different, why it matters, candidate portal, contact us)
• WHO WE ARE should be a drop down menu with link to pages (about us, mission, vision and purpose, our team)
• WHAT WE DO should be drop down menu with link to the following pages (IT Recruiting, IT Training, Hardware and software sales)
• What makes us different should be single page with different paragraph titles. (We live what we do, we don't compromise quality, we share knowledge, staffing guarantee)
• Why it matters should be single page with paragraph titles. (Quickly fill positions, candidate career development)
• Candidate portal should links to my portal login page. I can add the correct URL later. I just need it to link to somewhere. I can change it.
• Contact us should have (address, phone number, google map and a form to submit request for a call back)

```html
<!DOCTYPE html>
<html lang="en">
<head>
<meta charset="utf-8">
<title>Tovarin Business Solution</title>
<link rel="stylesheet" href="https://fonts.googleapis.com/css2?family=Lato:wght@400;700&family=Titillium+Web:wght@300;400;600&display=swap">
<style>
:root{
  --orange:#f9a34a;
  --orange-deep:#f08a1c;
  --blue:#0a4f9c;
  --ink:#1e1e1e;
  --text:#555;
  --muted:#8a8a8a;
  --light:#f3f3f3;
  --dark:#2a2a2a;
  --white:#fff;
}
*{box-sizing:border-box;margin:0;padding:0}
html,body{width:1200px;height:2941px;overflow:hidden}
body{font-family:"Lato",sans-serif;color:var(--text);background:var(--white);position:relative}
.section{position:absolute;left:0;width:1200px;overflow:hidden}
.abs{position:absolute}
h1,h2,h3{font-family:"Titillium Web",sans-serif;font-weight:400;color:var(--ink)}
.hl{color:var(--blue)}

/* top nav */
.topnav{top:0;height:55px;background:var(--orange);display:flex;justify-content:center;align-items:center;gap:38px}
.topnav a{color:var(--white);text-decoration:none;font-size:14px;font-weight:700;letter-spacing:.2px;text-transform:uppercase}
.topnav a.active{color:var(--blue)}

/* header */
.header{top:55px;height:82px;background:var(--white);box-shadow:0 2px 4px rgba(0,0,0,.08)}
.brand{left:78px;top:8px;font-family:"Titillium Web",sans-serif;font-weight:600;font-size:48px;color:var(--blue);line-height:60px}
.contact-chip{top:16px;display:flex;align-items:center;gap:12px}
.contact-chip .label{font-size:14px;color:var(--ink);text-transform:uppercase;line-height:16px}
.contact-chip .value{font-size:22px;color:var(--blue);line-height:26px}
.search{left:862px;top:18px;width:260px;height:44px;display:flex;border:1px solid #ddd}
.search span{flex:1;font-size:12px;color:#aaa;font-style:italic;padding:14px 14px}
.search .btn{width:44px;background:var(--blue);display:flex;align-items:center;justify-content:center}

/* hero */
.hero{top:137px;height:541px;background:linear-gradient(100deg,#d9dee3 0%,#e8ebee 40%,#c9d3dc 75%,#aebccb 100%)}
.hero-photo{left:0;top:0;width:1200px;height:541px}
.hero h1{left:78px;top:132px;font-size:58px;line-height:70px;text-transform:uppercase;color:#1b1b1b}
.hero .sub{left:80px;top:280px;font-family:"Titillium Web",sans-serif;font-size:30px;color:#333}
.hero .cta{left:78px;top:345px;width:207px;height:52px;border:2px solid #2b3a4a;color:var(--blue);font-size:15px;font-weight:700;display:flex;align-items:center;justify-content:center;text-transform:uppercase}

/* services */
.services{top:678px;height:396px;display:flex}
.service{width:400px;height:396px;background:var(--orange);position:relative;text-align:center}
.service.feature{background:var(--blue)}
.service .icon{position:absolute;left:150px;top:50px;width:100px;height:90px}
.service h3{position:absolute;left:0;width:400px;top:164px;font-size:22px;color:var(--blue)}
.service.feature h3{color:var(--white)}
.service p{position:absolute;left:30px;width:340px;top:208px;font-size:13px;line-height:22px;color:#8a5a20}
.service.feature p{color:var(--white)}
.service .more{position:absolute;left:178px;top:300px;width:44px;height:44px}

/* welcome */
.welcome{top:1074px;height:436px}
.welcome h2{left:0;width:1200px;top:36px;text-align:center;font-size:40px;text-transform:uppercase}
.welcome h2 .hl{text-transform:none}
.video{left:78px;top:125px;width:437px;height:261px;background:radial-gradient(circle at 60% 45%,#6aa7d8 0%,#1f4f82 45%,#0b2440 100%)}
.play{left:276px;top:235px;width:50px;height:50px}
.welcome .lead{left:582px;top:125px;width:530px;font-size:14px;font-weight:700;color:#333}
.welcome .body{left:582px;top:160px;width:530px;font-size:13.5px;line-height:23px}
.outline-btn{border:2px solid var(--blue);color:var(--blue);font-weight:700;font-size:14px;display:flex;align-items:center;justify-content:center;text-transform:uppercase}
.welcome .outline-btn{left:582px;top:330px;width:146px;height:52px}

/* business band */
.band{top:1510px;height:368px;background:linear-gradient(90deg,#3a2f28 0%,#5a4a3d 45%,#2e2a27 100%)}
.band-photo{left:0;top:0;width:1200px;height:368px}
.band h2{left:0;width:1200px;top:44px;text-align:center;font-size:40px;color:var(--white);text-transform:uppercase}
.band .sub{left:0;width:1200px;top:104px;text-align:center;font-family:"Titillium Web",sans-serif;font-size:20px;color:var(--white)}
.band .rule{left:400px;top:155px;width:400px;height:1px;background:rgba(255,255,255,.7)}
.band p{left:290px;width:620px;top:182px;text-align:center;font-size:15px;line-height:26px;color:var(--white)}
.band .btn-solid{left:444px;top:265px;width:146px;height:50px;background:var(--white);color:var(--blue);font-weight:700;font-size:14px;display:flex;align-items:center;justify-content:center;text-transform:uppercase}
.band .btn-ghost{left:610px;top:265px;width:146px;height:50px;border:2px solid var(--white);color:var(--white);font-weight:700;font-size:14px;display:flex;align-items:center;justify-content:center;text-transform:uppercase}

/* different + blog */
.split{top:1878px;height:447px}
.split h2{top:36px;font-size:40px}
.diff-title{left:78px}
.blog-title{left:624px}
.diff-intro{left:78px;top:118px;width:480px;font-size:13.5px;line-height:23px}
.ticks{left:78px;top:180px;width:480px;list-style:none}
.ticks li{display:flex;gap:12px;font-size:13.5px;line-height:23px;margin-bottom:8px}
.ticks svg{flex:none;margin-top:4px}
.post{left:624px;width:500px;height:124px}
.post .thumb{position:absolute;left:0;top:0;width:190px;height:124px}
.post .date{position:absolute;left:208px;top:0;font-size:11px;font-style:italic;color:var(--blue)}
.post h3{position:absolute;left:208px;top:16px;width:290px;font-family:"Lato",sans-serif;font-size:15px;line-height:23px;color:#333}
.post .line{position:absolute;left:208px;top:68px;width:290px;height:1px;background:#ddd}
.post p{position:absolute;left:208px;top:76px;width:290px;font-size:13.5px;line-height:22px;color:#777}

/* testimonials */
.clients{top:2325px;height:292px;background:var(--light)}
.clients h2{left:0;width:1200px;top:36px;text-align:center;font-size:40px}
.avatar{left:160px;top:125px;width:114px;height:114px;border-radius:50%;border:3px solid var(--blue);background:linear-gradient(160deg,#d8c9bb,#8f7a68)}
.clients blockquote{position:absolute;left:320px;top:122px;width:730px;font-size:13px;line-height:24px;font-style:italic;color:#666}
.clients .name{left:320px;top:212px;font-family:"Titillium Web",sans-serif;font-size:20px;color:var(--orange-deep)}
.arrow-l{left:30px;top:162px}
.arrow-r{left:1146px;top:162px}

/* footer */
.footer{top:2617px;height:261px;background:linear-gradient(90deg,#2b2b2b 0%,#3a3a3a 60%,#2d2d2d 100%)}
.footer-photo{left:0;top:0;width:1200px;height:261px}
.footer h4{position:absolute;top:36px;font-family:"Titillium Web",sans-serif;font-weight:400;font-size:20px;color:var(--white)}
.footer h4 span{color:var(--orange)}
.footer .uline{position:absolute;top:66px;height:1px;background:rgba(255,255,255,.3)}
.qlinks{left:78px;top:84px;list-style:none}
.qlinks li{font-size:13.5px;line-height:26px;color:var(--white)}
.cdetails{left:298px;top:84px;width:240px}
.cdetails .row{display:flex;gap:14px;font-size:13.5px;line-height:22px;color:var(--white);margin-bottom:16px}
.field{position:absolute;height:42px;background:#1e1e1e;border:1px solid #555;display:flex;align-items:center;gap:14px;padding-left:12px;font-size:13.5px;color:var(--white)}
.field.msg{align-items:flex-start;padding-top:12px}
.submit{left:836px;top:186px;width:106px;height:42px;background:var(--white);color:var(--blue);font-size:15px;display:flex;align-items:center;justify-content:center;text-transform:uppercase}

/* bottom bar */
.bottom{top:2878px;height:63px;background:var(--orange)}
.bottom .copy{left:78px;top:23px;font-size:13px;color:#333}
.bottom .copy b{color:var(--blue);font-weight:700}
.social{top:12px;width:40px;height:40px;border-radius:50%;border:2px solid var(--white);background:transparent}
</style>
</head>
<body>

<nav class="section topnav">
  <a class="active" href="#">Home</a>
  <a href="#">Who We Are</a>
  <a href="#">What We Do</a>
  <a href="#">What Make Us Different</a>
  <a href="#">Why It Matters</a>
  <a href="#">Candidate Portal</a>
  <a href="#">Contact Us</a>
</nav>

<header class="section header">
  <div class="abs brand">Tovarin</div>
  <div class="abs contact-chip" style="left:410px">
    <svg width="22" height="40" viewBox="0 0 22 40"><rect x="2" y="2" width="18" height="36" rx="3" fill="none" stroke="#f9a34a" stroke-width="3"/><line x1="8" y1="32" x2="14" y2="32" stroke="#f9a34a" stroke-width="3"/></svg>
    <div><div class="label">Call us on</div><div class="value">123.456.7890</div></div>
  </div>
  <div class="abs contact-chip" style="left:602px">
    <svg width="42" height="34" viewBox="0 0 42 34"><path d="M4 4h22v14H14l-6 6v-6H4z" fill="none" stroke="#f9a34a" stroke-width="2.5" stroke-linejoin="round"/><path d="M30 12h8v12h-4v5l-5-5H18v-3" fill="none" stroke="#f9a34a" stroke-width="2.5" stroke-linejoin="round"/></svg>
    <div><div class="label">Want to talk</div><div class="value">info@tovarin.com</div></div>
  </div>
  <div class="abs search"><span>Search Site here</span><div class="btn"><svg width="18" height="18" viewBox="0 0 18 18"><circle cx="7.5" cy="7.5" r="5.5" fill="none" stroke="#fff" stroke-width="2.5"/><line x1="11.5" y1="11.5" x2="16" y2="16" stroke="#fff" stroke-width="3"/></svg></div></div>
</header>

<section class="section hero">
  <div class="abs hero-photo" role="img" aria-label="Photo of a smiling professional working on a laptop in a bright office with colleagues behind"></div>
  <h1 class="abs">Are you ready to take<br>the next step?</h1>
  <div class="abs sub">We are there to keep you on the Right Path</div>
  <div class="abs cta">Contact us now</div>
</section>

<section class="section services">
  <div class="service">
    <svg class="icon" viewBox="0 0 100 90"><circle cx="28" cy="22" r="10" fill="none" stroke="#fff" stroke-width="4"/><circle cx="72" cy="22" r="10" fill="none" stroke="#fff" stroke-width="4"/><path d="M10 56c0-12 8-20 18-20M90 56c0-12-8-20-18-20" fill="none" stroke="#fff" stroke-width="4"/><circle cx="48" cy="44" r="18" fill="none" stroke="#fff" stroke-width="5"/><line x1="61" y1="57" x2="80" y2="80" stroke="#fff" stroke-width="8" stroke-linecap="round"/></svg>
    <h3>IT Recruiting</h3>
    <p>Lorem Ipsum is simply dummy text of the printing and typesetting industry. Lorem Ipsum has been the industry's standard dummy text ever.</p>
    <svg class="more" viewBox="0 0 44 44"><circle cx="22" cy="22" r="20" fill="none" stroke="#0a4f9c" stroke-width="2"/><path d="M15 15l7 7-7 7M23 15l7 7-7 7" fill="none" stroke="#0a4f9c" stroke-width="2"/></svg>
  </div>
  <div class="service feature">
    <svg class="icon" viewBox="0 0 100 90"><rect x="38" y="8" width="56" height="40" fill="none" stroke="#fff" stroke-width="4"/><line x1="66" y1="48" x2="58" y2="66" stroke="#fff" stroke-width="3"/><line x1="66" y1="48" x2="74" y2="66" stroke="#fff" stroke-width="3"/><circle cx="22" cy="30" r="9" fill="#fff"/><path d="M8 86V54c0-8 6-13 14-13l20-8 3 6-16 9v38z" fill="#fff"/></svg>
    <h3>IT Training</h3>
    <p>Lorem Ipsum is simply dummy text of the printing and typesetting industry. Lorem Ipsum has been the industry's standard dummy text ever.</p>
    <svg class="more" viewBox="0 0 44 44"><circle cx="22" cy="22" r="20" fill="none" stroke="#fff" stroke-width="2"/><path d="M15 15l7 7-7 7M23 15l7 7-7 7" fill="none" stroke="#fff" stroke-width="2"/></svg>
  </div>
  <div class="service">
    <svg class="icon" viewBox="0 0 100 90"><rect x="4" y="6" width="92" height="60" rx="5" fill="none" stroke="#fff" stroke-width="5"/><line x1="4" y1="54" x2="96" y2="54" stroke="#fff" stroke-width="4"/><path d="M40 66l-4 16h28l-4-16" fill="#fff"/></svg>
    <h3>Hardware &amp; Software Sales</h3>
    <p>Lorem Ipsum is simply dummy text of the printing and typesetting industry. Lorem Ipsum has been the industry's standard dummy text ever.</p>
    <svg class="more" viewBox="0 0 44 44"><circle cx="22" cy="22" r="20" fill="none" stroke="#0a4f9c" stroke-width="2"/><path d="M15 15l7 7-7 7M23 15l7 7-7 7" fill="none" stroke="#0a4f9c" stroke-width="2"/></svg>
  </div>
</section>

<section class="section welcome">
  <h2 class="abs">Welcome to <span class="hl">Tovarin</span></h2>
  <div class="abs video" role="img" aria-label="Video still of a businessman touching glowing digital bubbles"></div>
  <svg class="abs play" viewBox="0 0 50 50"><circle cx="25" cy="25" r="24" fill="rgba(0,0,0,.55)"/><path d="M20 15l14 10-14 10z" fill="#fff"/></svg>
  <p class="abs lead">Lorem Ipsum is simply dummy text of the printing and typesetting industry.</p>
  <p class="abs body">Lorem Ipsum has been the industry's standard dummy text ever since the 1500s, when an unknown printer took a galley of type and scrambled it to make a type specimen book. It has survived not only five centuries, but also the leap into electronic typesetting, remaining essentially unchanged. It was popularised in the 1960s with the release of Letraset sheets containing Lorem Ipsum passages, and more recently with desktop publishing.</p>
  <div class="abs outline-btn">Read more</div>
</section>

<section class="section band">
  <div class="abs band-photo" role="img" aria-label="Photo of hands at a laptop and coffee cup on a wooden desk"></div>
  <h2 class="abs">Business Solutions</h2>
  <div class="abs sub">For you at your Door Steps</div>
  <div class="abs rule"></div>
  <p class="abs">Lorem Ipsum is simply dummy text of the printing and typesetting industry. Lorem Ipsum has been the industry's standard dummy text ever.</p>
  <div class="abs btn-solid">Get started</div>
  <div class="abs btn-ghost">Know more</div>
</section>

<section class="section split">
  <h2 class="abs diff-title">What Makes Us <span class="hl">Different</span></h2>
  <h2 class="abs blog-title">Latest <span class="hl">Blog</span> Post</h2>
  <p class="abs diff-intro">Lorem Ipsum is simply dummy text of the printing and typesetting industry. Lorem Ipsum has been the industry's standard.</p>
  <ul class="abs ticks">
    <li><svg width="16" height="16" viewBox="0 0 16 16"><rect x="1" y="3" width="12" height="12" fill="none" stroke="#f9a34a" stroke-width="1.5"/><path d="M4 8l3 3 8-9" fill="none" stroke="#f9a34a" stroke-width="2"/></svg><span>Lorem Ipsum is simply dummy text of the printing and typesetting industry. Lorem Ipsum has been the industry's standard.</span></li>
    <li><svg width="16" height="16" viewBox="0 0 16 16"><rect x="1" y="3" width="12" height="12" fill="none" stroke="#f9a34a" stroke-width="1.5"/><path d="M4 8l3 3 8-9" fill="none" stroke="#f9a34a" stroke-width="2"/></svg><span>Lorem Ipsum is simply dummy text of the printing and typesetting.</span></li>
    <li><svg width="16" height="16" viewBox="0 0 16 16"><rect x="1" y="3" width="12" height="12" fill="none" stroke="#f9a34a" stroke-width="1.5"/><path d="M4 8l3 3 8-9" fill="none" stroke="#f9a34a" stroke-width="2"/></svg><span>Lorem Ipsum is simply dummy text of the printing.</span></li>
    <li><svg width="16" height="16" viewBox="0 0 16 16"><rect x="1" y="3" width="12" height="12" fill="none" stroke="#f9a34a" stroke-width="1.5"/><path d="M4 8l3 3 8-9" fill="none" stroke="#f9a34a" stroke-width="2"/></svg><span>Lorem Ipsum is simply dummy text of the printing and typesetting industry.</span></li>
    <li><svg width="16" height="16" viewBox="0 0 16 16"><rect x="1" y="3" width="12" height="12" fill="none" stroke="#f9a34a" stroke-width="1.5"/><path d="M4 8l3 3 8-9" fill="none" stroke="#f9a34a" stroke-width="2"/></svg><span>Lorem Ipsum has been the industry's standard.</span></li>
  </ul>
  <article class="abs post" style="top:122px">
    <div class="thumb" role="img" aria-label="Photo of a team meeting around a table" style="background:linear-gradient(135deg,#cfe0ee,#7d9fbd)"></div>
    <div class="date">March 5,2016</div>
    <h3>Lorem Ipsum is simply dummy text of the printing.</h3>
    <div class="line"></div>
    <p>Lorem Ipsum is simply dummy text of the printing and typesetting industry.</p>
  </article>
  <article class="abs post" style="top:268px">
    <div class="thumb" role="img" aria-label="Photo of a businessperson walking with a briefcase" style="background:linear-gradient(135deg,#e7d3cf,#9c7f7d)"></div>
    <div class="date">March 5,2016</div>
    <h3>Lorem Ipsum is simply dummy text of the printing.</h3>
    <div class="line"></div>
    <p>Lorem Ipsum is simply dummy text of the printing and typesetting industry.</p>
  </article>
</section>

<section class="section clients">
  <h2 class="abs">What Our <span class="hl">Clients</span> Say</h2>
  <svg class="abs arrow-l" width="24" height="44" viewBox="0 0 24 44"><path d="M22 2L2 22l20 20" fill="none" stroke="#0a4f9c" stroke-width="1.5"/></svg>
  <div class="abs avatar" role="img" aria-label="Client portrait"></div>
  <blockquote>"Lorem Ipsum is simply dummy text of the printing and typesetting industry. Lorem Ipsum has been the industry's standard dummy text ever since the 1500s, when an unknown printer took a galley of type and scrambled it to make a type specimen book."</blockquote>
  <div class="abs name">Daniel Morrow</div>
  <svg class="abs arrow-r" width="24" height="44" viewBox="0 0 24 44"><path d="M2 2l20 20L2 42" fill="none" stroke="#0a4f9c" stroke-width="1.5"/></svg>
</section>

<footer class="section footer">
  <div class="abs footer-photo" role="img" aria-label="Dimmed photo of people working at office desks"></div>
  <h4 style="left:78px">Quick <span>Links</span></h4>
  <div class="uline" style="left:78px;width:190px"></div>
  <ul class="abs qlinks">
    <li>• Home</li><li>• About</li><li>• Services</li><li>• Team</li><li>• Career</li><li>• Contact</li>
  </ul>
  <h4 style="left:298px">Contact <span>Details</span></h4>
  <div class="uline" style="left:298px;width:240px"></div>
  <div class="abs cdetails">
    <div class="row"><svg width="14" height="20" viewBox="0 0 14 20"><path d="M7 19C2 12 1 10 1 7a6 6 0 0112 0c0 3-1 5-6 12z" fill="#f9a34a"/><circle cx="7" cy="7" r="2.3" fill="#333"/></svg><span>123 Building Name, Street,<br>City, Country - Zip code</span></div>
    <div class="row"><svg width="14" height="16" viewBox="0 0 14 16"><path d="M3 1l3 4-2 2c1 2 3 4 5 5l2-2 3 3-2 3C6 15 0 9 1 3z" fill="#f9a34a"/></svg><span>123-4567-890</span></div>
    <div class="row"><svg width="16" height="12" viewBox="0 0 16 12"><rect x="0" y="0" width="16" height="12" fill="#f9a34a"/><path d="M0 0l8 6 8-6" fill="none" stroke="#333" stroke-width="1.4"/></svg><span>info@tovarin.com</span></div>
  </div>
  <h4 style="left:578px">Quick <span>Inquiry</span></h4>
  <div class="uline" style="left:578px;width:530px"></div>
  <div class="field" style="left:578px;top:80px;width:247px"><svg width="14" height="14" viewBox="0 0 14 14"><circle cx="7" cy="4" r="3.5" fill="#fff"/><path d="M0 14c0-5 3-7 7-7s7 2 7 7z" fill="#fff"/></svg>Your Name:</div>
  <div class="field" style="left:578px;top:132px;width:247px"><svg width="14" height="11" viewBox="0 0 14 11"><rect width="14" height="11" fill="#fff"/><path d="M0 0l7 6 7-6" fill="none" stroke="#1e1e1e" stroke-width="1.4"/></svg>E-Mail Address:</div>
  <div class="field" style="left:578px;top:184px;width:247px"><svg width="12" height="14" viewBox="0 0 12 14"><path d="M0 0h8l4 4v10H0z" fill="#fff"/></svg>Subject:</div>
  <div class="field msg" style="left:838px;top:80px;width:270px;height:90px"><svg width="14" height="14" viewBox="0 0 14 14"><path d="M1 13l1-4 8-8 3 3-8 8z" fill="#fff"/></svg>Message:</div>
  <div class="abs submit">Submit</div>
</footer>

<div class="section bottom">
  <div class="abs copy">© <b>Tovarin</b> 2016. All Rights Reserved</div>
  <div class="abs social" style="left:976px" aria-label="Social link one"></div>
  <div class="abs social" style="left:1028px" aria-label="Social link two"></div>
  <div class="abs social" style="left:1080px" aria-label="Social link three"></div>
</div>

</body>
</html>
```